Ridgeline Journeys business card

please see website
www.ridgelinejourneys.comau

info needed on card
Curtis Halvey
Ph
email
Adventure Riding GPS trails

please use my logo and colours off my site

Curtis Halvey
curtis@ridgelinejourneys.com

```html
<!DOCTYPE html>
<html lang="en">
<head>
<meta charset="utf-8">
<title>Ridgeline Journeys — Business Card</title>
<link rel="stylesheet" href="https://fonts.googleapis.com/css2?family=Open+Sans:wght@400;600;800&display=swap">
<style>
  :root {
    --backdrop-top: #2b2b2b;
    --backdrop-bottom: #050505;
    --card-white: #f3f3f3;
    --brand-yellow: #ffd200;
    --brand-yellow-light: #fff33d;
    --accent-yellow: #f5d311;
    --ink: #111111;
    --mark-grey: #5e5e5e;
  }
  html, body {
    margin: 0;
    padding: 0;
    width: 1200px;
    height: 900px;
    overflow: hidden;
  }
  body {
    position: relative;
    background: linear-gradient(180deg, var(--backdrop-top) 0%, var(--backdrop-bottom) 100%);
    font-family: "Open Sans", Arial, sans-serif;
    color: var(--ink);
  }
  .card {
    position: absolute;
    top: 184px;
    height: 490px;
    border-radius: 12px;
    overflow: hidden;
    box-shadow: 0 2px 10px rgba(0,0,0,0.45);
  }
  .card-front {
    left: 299px;
    width: 301px;
    background: var(--card-white);
  }
  .card-back {
    left: 645px;
    width: 305px;
    background: linear-gradient(180deg, var(--brand-yellow) 0%, var(--brand-yellow-light) 100%);
  }
  .brand-lockup {
    position: absolute;
    left: 32px;
    top: 226px;
    top: 42px;
    display: flex;
    align-items: center;
    gap: 14px;
  }
  .brand-square {
    width: 54px;
    height: 54px;
    background: var(--brand-yellow);
  }
  .brand-name {
    font-weight: 800;
    font-size: 25px;
    line-height: 29px;
    color: var(--ink);
    letter-spacing: 0.2px;
  }
  .contact {
    position: absolute;
    left: 0;
    right: 0;
    top: 346px;
    text-align: center;
  }
  .contact-name {
    font-weight: 600;
    font-size: 16px;
    color: var(--accent-yellow);
    margin: 0 0 10px;
  }
  .contact-line {
    font-size: 13.5px;
    line-height: 20px;
    margin: 0;
    display: flex;
    justify-content: center;
    align-items: center;
    gap: 4px;
  }
  .contact-line svg {
    width: 11px;
    height: 11px;
    fill: var(--accent-yellow);
  }
  .back-name {
    position: absolute;
    left: 0;
    right: 0;
    top: 332px;
    text-align: center;
    font-weight: 800;
    color: var(--ink);
    margin: 0;
    line-height: 1;
  }
  .back-name .line-one { display: block; font-size: 36px; margin-bottom: 6px; }
  .back-name .line-two { display: block; font-size: 42px; }
  .tagline {
    position: absolute;
    left: 0;
    right: 0;
    top: 436px;
    text-align: center;
    font-weight: 600;
    font-size: 14.5px;
    letter-spacing: 0.2px;
    margin: 0;
    color: var(--ink);
  }
</style>
</head>
<body>
  <section class="card card-front">
    <div class="brand-lockup">
      <div class="brand-square"></div>
      <div class="brand-name">Ridgeline<br>Journeys</div>
    </div>
    <div class="contact">
      <p class="contact-name">Curtis Halvey</p>
      <p class="contact-line">
        <svg viewBox="0 0 12 12" aria-hidden="true"><path d="M1 3c0-1 1-2 2-2h6c1 0 2 1 2 2v1H8V3H4v1H1z M2 5h8l1 5H1z"/></svg>
        (044)-555-0142
      </p>
      <p class="contact-line">
        <svg viewBox="0 0 12 12" aria-hidden="true"><path d="M1 2h10v8H1z M1 2l5 4 5-4" stroke="#f3f3f3" stroke-width="0.8"/></svg>
        curtis@ridgelinejourneys.com
      </p>
      <p class="contact-line">
        <svg viewBox="0 0 12 12" aria-hidden="true"><path d="M8 1l3 3-6 6H2V7z"/></svg>
        www.ridgelinejourneys.com
      </p>
    </div>
  </section>

  <section class="card card-back">
    <h1 class="back-name"><span class="line-one">Ridgeline</span><span class="line-two">Journeys</span></h1>
    <p class="tagline">ADVENTURE RIDING GPS TRAILS</p>
  </section>
</body>
</html>
```